Fantasy Football UX Style Guide & Sample Pages (QWR - not soccer)

Happy April designers!! We are looking to establish a relationship with a killer designer who can work with us on establishing an exciting, professional UX that is delivers a great experience and leverages the powerful technologies of react.js and other 2015 advancements.

Our ideal design team can be one or more people -- but is responsive to feedback, has "no ego" in his/her designs and is willing to go the extra mile to get the job done well. We expect several iterations before any design is considered final. If this excites you - jump in!! If you think working together in an iterative fashion would frustrate you -- please stop now. We will give lots of feedback and ideas. The UX resulting is very important to us.

The site that we are building is related to QWR football. If you have no experience watching American QWR Football -- please stop reading. If you enjoy this game and would like to design UX elements that have an affinity -- please join this design contest.

As a starter project -- we are going to ask that someone review the designs that we have received for a variety of project design competitions. You will notice that they are all pretty disjointed (from our opinion) and also a little 2005 from a design perspective. The winner from this competition will assemble an accepted, killer design that will bring all of these "pages" together into a common design. We would like to see each page in the concept.

Ultimately, what this amounts to is a common style guide that delivers on the strength of the existing brand & logo (files 1 & 2) --- and hopefully -- takes it, and the pages to the next level.

Please note: While our ideal partner will give us an iteration of each page in the new design style guide -- the style guide itself is what is the most important deliverable. We won't expect every page to be perfect. We realize that will take some additional project work.

Target Market(s)

fantasy sports players

Industry/Entity Type

Work

Number of Pages Required

5+ page

Font styles to use
Serif
Sans Serif

Colors
ec1f27
ffffff
161616
959595

Requirements
Must have
• Must Have:
• - A strong sense of brand (please feel free to ask questions; logo is in file 1 & 2)
• - A strong understanding of what resonates with fantasy football players
• - A STYLE GUIDE -- I mention this above but this our primary deliverable for this project. We are looking for an awesome style guide that can be used to deliver any page / mobile app regardless of what is on it. [file attached for example of what a proper style guide looks like. We would like to see this expanded upon]
• - We are looking to see the style guide applied to a variety of page types (examples are shared in the files below -- home page, blog home page, blog item page, specific pages of importance.) This will give us a sense of how the style guide holds up and if we need some new areas addressed in it.
• - We recognize that each page doesn't have to be pixel perfect, and we are willing to take that on as additional project work if the designer would like it.
• - An design that is "easy to read" but conveys excitement
• - We deal with a lot of "sports analytics" so understanding what makes for a good chart is helpful. (if you want to use examples from d3, that is even better)
• - An understanding for how to visualize date & trends in data (see above)
• - A modern REACT.JS like look; not looking for styles from 10 years ago
Nice to have
• - Fresh new takes on the layouts included here.
• - Suggestions for how to make the logo more 2015
• - Creative, visionary ideas
• - Questions for what the screens attached are meant to portray (we'd rather you ask)
Should not have
• - A new logo or color palette. We like what we have and have an established presence here.
• - We are looking for pure, kick-ass design at this point. We don't want it coded.
• - There are many elements that we like from the concept pages below. You don't have to redesign everything. What we don't like is that the UX is not great, and there is no common styling. Also the design itself feels a little "dated" and "dark" in some areas. We are hoping for something more exciting and fresh.

```html
<!DOCTYPE html>
<html lang="en">
<head>
<meta charset="utf-8">
<title>Gridline – Fantasy Football</title>
<link rel="stylesheet" href="https://fonts.googleapis.com/css2?family=Oswald:wght@400;500&family=Open+Sans:wght@400;600&display=swap">
<style>
:root{
  --red:#ec1f27;
  --red-deep:#b3121a;
  --red-band:#7d0a10;
  --red-band-dark:#5c060b;
  --ink:#161616;
  --panel:#222222;
  --grey:#959595;
  --text:#555555;
  --white:#ffffff;
  --rule:#dddddd;
}
*{box-sizing:border-box;margin:0;padding:0}
html,body{width:1200px;height:2609px;overflow:hidden;background:var(--white)}
body{position:relative;font-family:'Open Sans',Arial,sans-serif;color:var(--text)}
h2,h3{font-weight:400}

/* header */
.site-header{position:absolute;left:0;top:0;width:1200px;height:91px;background:var(--ink)}
.brand{position:absolute;left:99px;top:30px;font-family:'Oswald',sans-serif;font-size:24px;font-weight:500;color:var(--red);letter-spacing:1px;display:flex;align-items:center;gap:8px;line-height:32px}
.brand-square{width:14px;height:14px;background:var(--red)}
.nav-item{position:absolute;top:0;height:91px;line-height:91px;font-family:'Oswald',sans-serif;font-size:15px;color:var(--white);text-transform:uppercase;white-space:nowrap}
.nav-item.active{background:var(--red);width:51px;text-align:center}
.btn{position:absolute;background:var(--red-deep);color:var(--white);font-family:'Oswald',sans-serif;text-transform:uppercase;text-align:center;border-radius:2px;white-space:nowrap}
.header-btn{top:33px;height:32px;line-height:32px;font-size:14px}

/* hero */
.hero{position:absolute;left:0;top:91px;width:1200px;height:513px;background:radial-gradient(ellipse at 60% 35%,#3a4557 0%,#1b2230 45%,#0c0f15 100%)}
.hero-photo{position:absolute;left:520px;top:0;width:560px;height:513px;background:radial-gradient(ellipse at 50% 40%,#c9ccd2 0%,#7d8390 35%,rgba(30,36,48,0) 70%)}
.hero-kicker{position:absolute;left:99px;top:118px;font-size:35px;line-height:44px;color:var(--white);font-family:'Oswald',sans-serif;font-weight:400}
.hero-title{position:absolute;left:97px;top:160px;font-size:68px;line-height:84px;color:var(--white);font-family:'Oswald',sans-serif;font-weight:400;letter-spacing:-0.5px}
.hero-btn{left:99px;top:278px;width:105px;height:53px;line-height:53px;font-size:21px}
.dot{position:absolute;top:369px;width:9px;height:9px;border-radius:50%;background:#3b3f47}
.dot.on{background:var(--red)}

/* sections */
.section-title{position:absolute;left:0;width:1200px;text-align:center;font-family:'Oswald',sans-serif;font-size:35px;line-height:44px;color:var(--ink);text-transform:uppercase}
.title-rule{position:absolute;left:471px;width:256px;height:4px;background:var(--rule)}
.title-rule::after{content:"";position:absolute;left:112px;top:0;width:35px;height:4px;background:var(--red)}
.card{position:absolute;width:303px}
.card-photo{width:303px;height:153px}
.card-title{margin-top:22px;font-family:'Oswald',sans-serif;font-size:16px;line-height:26px;color:var(--red);text-transform:uppercase}
.card-text{margin-top:12px;font-size:12.5px;line-height:21px;color:var(--text)}
.view-btn{left:541px;width:119px;height:38px;line-height:38px;font-size:15px}

/* red band */
.band{position:absolute;left:0;top:1176px;width:1200px;height:545px;background:linear-gradient(135deg,var(--red-band) 0%,#9a0d14 35%,var(--red-band-dark) 70%,#860a11 100%)}
.panel{position:absolute;width:318px;height:392px;background:var(--panel)}
.panel-head{height:51px;line-height:51px;padding-left:16px;background:linear-gradient(180deg,#e0232b,#b8141b);font-family:'Oswald',sans-serif;font-size:16px;color:var(--white);text-transform:uppercase}
.item{position:absolute;left:18px;width:290px;height:77px}
.item-thumb{position:absolute;left:0;top:0;width:81px;height:77px}
.item-title{position:absolute;left:95px;top:2px;width:195px;font-family:'Oswald',sans-serif;font-size:12px;line-height:20px;color:var(--white);text-transform:uppercase}
.item-meta{position:absolute;left:95px;top:48px;font-size:12px;line-height:18px;color:var(--red);white-space:nowrap}
.video-main{position:absolute;left:0;top:61px;width:318px;height:219px;background:radial-gradient(ellipse at 50% 45%,#3c5872 0%,#18222e 70%)}
.play{position:absolute;left:144px;top:94px}
.video-label{position:absolute;right:8px;bottom:10px;font-family:'Oswald',sans-serif;font-size:20px;color:var(--white)}
.video-thumb{position:absolute;top:290px;width:100px;height:102px}

/* footer */
.site-footer{position:absolute;left:0;top:2303px;width:1200px;height:252px;background:linear-gradient(135deg,#8a0b12 0%,#6d070d 50%,#8f0d14 100%)}
.footer-head{position:absolute;top:42px;font-family:'Oswald',sans-serif;font-size:16px;color:var(--white);text-transform:uppercase}
.footer-text{position:absolute;font-size:12.5px;line-height:21px;color:#d98a8e}
.social{position:absolute;width:42px;height:42px}
.bottom-bar{position:absolute;left:0;top:2555px;width:1200px;height:54px;background:var(--white)}
.copyright{position:absolute;left:99px;top:18px;font-size:12px;color:var(--ink)}
.foot-link{position:absolute;top:18px;font-family:'Oswald',sans-serif;font-size:12px;color:var(--ink);text-transform:uppercase;white-space:nowrap}
.foot-link.active{color:var(--red)}
</style>
</head>
<body>

<header class="site-header">
  <div class="brand"><span class="brand-square"></span>GRIDLINE</div>
  <div class="nav-item active" style="left:377px">Home</div>
  <div class="nav-item" style="left:453px">Latest Articles</div>
  <div class="nav-item" style="left:578px">Fantasy Football News</div>
  <div class="nav-item" style="left:750px">Fantasy Football Advice</div>
  <div class="btn header-btn" style="left:929px;width:73px">Log In</div>
  <div class="btn header-btn" style="left:1012px;width:89px">Register</div>
</header>

<section class="hero">
  <div class="hero-photo" role="img" aria-label="Football player in white helmet and jersey charging forward with the ball"></div>
  <div class="hero-kicker">THE WORLD</div>
  <div class="hero-title">CHAMPIONSHIP</div>
  <div class="btn hero-btn">Results</div>
  <span class="dot on" style="left:99px"></span>
  <span class="dot" style="left:119px"></span>
  <span class="dot" style="left:139px"></span>
</section>

<h2 class="section-title" style="top:638px">Top Stories</h2>
<div class="title-rule" style="top:703px"></div>

<article class="card" style="left:99px;top:752px">
  <div class="card-photo" role="img" aria-label="Receiver reaching up for the ball under a blue sky" style="background:linear-gradient(160deg,#2f6fc4,#8fb6e6 60%,#d7dde6)"></div>
  <h3 class="card-title">2014 QWR free agent WRs rising a. falling on new teams RBs</h3>
  <p class="card-text">Neque porro quisquam est, qui dolorem ipsum quia dolor sit amet, consectetur, adipisci velit, sed quia non numquam eius...</p>
</article>
<article class="card" style="left:449px;top:752px">
  <div class="card-photo" role="img" aria-label="Player in red jersey on a stadium field" style="background:linear-gradient(180deg,#6a4a3a,#7b2323 50%,#3d5a2c)"></div>
  <h3 class="card-title">Rick Dolan getting plenty of love in early rankings</h3>
  <p class="card-text">Neque porro quisquam est, qui dolorem ipsum quia dolor sit amet, consectetur, adipisci velit, sed quia non numquam eius...</p>
</article>
<article class="card" style="left:799px;top:752px">
  <div class="card-photo" role="img" aria-label="Football helmet close-up on black background" style="background:linear-gradient(90deg,#050505 30%,#6a6a6a 75%,#c8c8c8)"></div>
  <h3 class="card-title">Fantasy football rookies: position review for WRs scoring NBS</h3>
  <p class="card-text">Neque porro quisquam est, qui dolorem ipsum quia dolor sit amet, consectetur, adipisci velit, sed quia non numquam eius...</p>
</article>
<div class="btn view-btn" style="top:1087px">View All</div>

<section class="band">
  <div class="panel" style="left:99px;top:77px">
    <div class="panel-head">Player News</div>
    <div class="item" style="top:91px">
      <div class="item-thumb" role="img" aria-label="Player catching a pass" style="background:linear-gradient(160deg,#6f8fb8,#4f7a3a)"></div>
      <div class="item-title">2014 QWR free agent WRs rising an falling on new teams...</div>
      <div class="item-meta">Team &nbsp;|&nbsp; Player Name &nbsp;|&nbsp; QB</div>
    </div>
    <div class="item" style="top:189px">
      <div class="item-thumb" role="img" aria-label="Players in a tackle" style="background:linear-gradient(160deg,#e0e0e0,#2a3a6a)"></div>
      <div class="item-title">2014 QWR free agent WRs rising an falling on new teams...</div>
      <div class="item-meta">Team &nbsp;|&nbsp; Player Name &nbsp;|&nbsp; QB</div>
    </div>
    <div class="item" style="top:285px">
      <div class="item-thumb" role="img" aria-label="Player in white jersey running" style="background:linear-gradient(160deg,#d8d8d8,#2a3c70)"></div>
      <div class="item-title">2014 QWR free agent WRs rising an falling on new teams...</div>
      <div class="item-meta">Team &nbsp;|&nbsp; Player Name &nbsp;|&nbsp; QB</div>
    </div>
  </div>

  <div class="panel" style="left:442px;top:77px;background:transparent">
    <div class="panel-head">Featured Video</div>
    <div class="video-main" role="img" aria-label="Video still of players at a night game">
      <svg class="play" width="30" height="30" viewBox="0 0 30 30"><circle cx="15" cy="15" r="12" fill="none" stroke="#fff" stroke-width="2.5"/><path d="M12 9.5 L20 15 L12 20.5Z" fill="#fff"/></svg>
      <span class="video-label">Vidstream</span>
    </div>
    <div class="video-thumb" role="img" aria-label="Video thumbnail of a tackle" style="left:0;background:linear-gradient(160deg,#4a5a3a,#2f4a22)"></div>
    <div class="video-thumb" role="img" aria-label="Video thumbnail of players in orange" style="left:109px;background:linear-gradient(160deg,#7a4a2a,#3a3a2a)"></div>
    <div class="video-thumb" role="img" aria-label="Video thumbnail of player in green" style="left:218px;background:linear-gradient(160deg,#2a5a3a,#5a7a3a)"></div>
  </div>

  <div class="panel" style="left:783px;top:77px">
    <div class="panel-head">Fantasy Offseason</div>
    <div class="item" style="top:91px">
      <div class="item-thumb" role="img" aria-label="Player in red jersey" style="background:linear-gradient(160deg,#b83030,#6a8a4a)"></div>
      <div class="item-title">2014 QWR free agent WRs rising and falling on new teams trouble brewing</div>
    </div>
    <div class="item" style="top:189px">
      <div class="item-thumb" role="img" aria-label="Player in red and white uniform" style="background:linear-gradient(160deg,#c04040,#d8d8d8)"></div>
      <div class="item-title">2014 QWR free agent WRs rising and falling on new teams trouble brewing</div>
    </div>
    <div class="item" style="top:285px">
      <div class="item-thumb" role="img" aria-label="Player carrying the ball" style="background:linear-gradient(160deg,#8a3030,#5a6a3a)"></div>
      <div class="item-title">2014 QWR free agent WRs rising and falling on new teams trouble brewing</div>
    </div>
  </div>
</section>

<h2 class="section-title" style="top:1751px">Recent Blog</h2>
<div class="title-rule" style="top:1816px"></div>

<article class="card" style="left:99px;top:1864px">
  <div class="card-photo" role="img" aria-label="Black and white player in helmet" style="background:linear-gradient(180deg,#2a2a2a,#9a9a9a 60%,#444)"></div>
  <h3 class="card-title">2014 QWR free agent WRs rising a. falling on new teams RBs</h3>
  <p class="card-text">Neque porro quisquam est, qui dolorem ipsum quia dolor sit amet, consectetur, adipisci velit, sed quia non numquam eius...</p>
</article>
<article class="card" style="left:449px;top:1864px">
  <div class="card-photo" role="img" aria-label="Silhouettes of players against a bright blue sky" style="background:radial-gradient(ellipse at 60% 60%,#b8e4ff,#2a7ad0 50%,#0a2a6a)"></div>
  <h3 class="card-title">Rick Dolan getting plenty of love in early rankings</h3>
  <p class="card-text">Neque porro quisquam est, qui dolorem ipsum quia dolor sit amet, consectetur, adipisci velit, sed quia non numquam eius...</p>
</article>
<article class="card" style="left:799px;top:1864px">
  <div class="card-photo" role="img" aria-label="Players lined up at the scrimmage in a packed stadium" style="background:linear-gradient(180deg,#8a5a4a,#c84040 50%,#4a6a3a)"></div>
  <h3 class="card-title">Fantasy football rookies: position review for WRs scoring NBS</h3>
  <p class="card-text">Neque porro quisquam est, qui dolorem ipsum quia dolor sit amet, consectetur, adipisci velit, sed quia non numquam eius...</p>
</article>
<div class="btn view-btn" style="top:2198px">View All</div>

<footer class="site-footer">
  <div class="footer-head" style="left:99px">About Gridline</div>
  <p class="footer-text" style="left:99px;top:82px;width:270px">Neque porro quisquam est, qui dolorem ipsum quia dolor sit amet, consectetur, adipisci velit, sed quia non numquam eius...</p>

  <div class="footer-head" style="left:472px">Follow Us</div>
  <div class="social" aria-label="Social link" style="left:472px;top:89px;background:#3b5998"></div>
  <div class="social" aria-label="Social link" style="left:524px;top:89px;background:#1da1f2"></div>
  <div class="social" aria-label="Social link" style="left:576px;top:89px;background:#0e76a8"></div>
  <div class="social" aria-label="Social link" style="left:628px;top:89px;background:#8a5a44"></div>
  <div class="social" aria-label="Social link" style="left:680px;top:89px;background:#f26522"></div>
  <div class="social" aria-label="Social link" style="left:472px;top:142px;background:#cd201f"></div>
  <div class="social" aria-label="Social link" style="left:524px;top:142px;background:#bd081c"></div>
  <div class="social" aria-label="Social link" style="left:576px;top:142px;background:#ea4c89"></div>
  <div class="social" aria-label="Social link" style="left:628px;top:142px;background:#d34836"></div>
  <div class="social" aria-label="Social link" style="left:680px;top:142px;background:#00aff0"></div>

  <div class="footer-head" style="left:839px">Contact Us</div>
  <p class="footer-text" style="left:839px;top:82px;width:270px">Neque porro quisquam est, qui dolorem ipsum quia dolor sit amet.</p>
  <p class="footer-text" style="left:839px;top:143px">1800-555-019<br>info@gridline-hub.com</p>
</footer>

<div class="bottom-bar">
  <div class="copyright">© 2015 gridline-hub.com. All rights reserved.</div>
  <div class="foot-link active" style="left:659px">Home</div>
  <div class="foot-link" style="left:717px">Latest Articles</div>
  <div class="foot-link" style="left:826px">Fantasy Football News</div>
  <div class="foot-link" style="left:976px">Fantasy Football Advice</div>
</div>

</body>
</html>
```